New Business Card Design Project LORVANTI-Italy

we are LORVANTI-Italy
our company in the market for 3 years we are luxury cosmetic company and its about time for a facelift :)
i will like to have elegant luxurious and unique business card
that will give the person that get it a unique, luxurious and elegant impression
I'm VERY OPEN FOR NEW IDEAS , even duo i add a few files of things that i see on line and i like them

i add my logo as well
my website is LORVANTI.COM
(if you would like to see the main style that we have)

Target Market(s)

adult that have money :)

Industry/Entity Type

Business

Contact Information for Business Card

Name - Dario Lorvanti
Position - CEO and CO Founder
address - 4817 E Halvern
telephone - 555-384-1926
email - dario@lorvanti.com
fax - 555-384-1926
website - LORVANTI.COM

Colors
000000
959595
fbee3e
ffffff

Requirements
Must have
• big logo in GOLD color
• elegant look
• impressive
Nice to have
• not must but maybe classy pattern background
• not must but maybe emblem
• maybe clear plastic business card
Should not have
• colors
• images

```html
<!DOCTYPE html>
<html lang="en">
<head>
<meta charset="utf-8">
<title>LORVANTI Italy – Business Card</title>
<link rel="stylesheet" href="https://fonts.googleapis.com/css2?family=Cormorant+Garamond:wght@600&family=PT+Sans:wght@400&display=swap">
<style>
  :root {
    --page: #e7e5e3;
    --card-black: #000000;
    --gold: #d8a92a;
    --gold-soft: #e4bc45;
    --white: #ffffff;
    --frost-a: #ebe8e7;
    --frost-b: #f7f5f4;
    --frost-edge: #dcd8d6;
  }
  * { margin: 0; padding: 0; box-sizing: border-box; }
  html, body {
    width: 1200px;
    height: 900px;
    overflow: hidden;
    background: var(--page);
  }
  .business-card {
    position: absolute;
    left: 150px;
    top: 173px;
    width: 900px;
    height: 554px;
    background: var(--card-black);
    border-radius: 17px;
    overflow: hidden;
    font-family: "PT Sans", Arial, sans-serif;
    color: var(--white);
  }
  .frost-band {
    position: absolute;
    left: 0;
    top: 0;
    width: 900px;
    height: 554px;
  }
  .holder {
    position: absolute;
    right: 48px;
    top: 42px;
    text-align: right;
  }
  .holder-name {
    font-family: "Cormorant Garamond", "Times New Roman", serif;
    font-weight: 600;
    font-size: 35px;
    letter-spacing: 1px;
    line-height: 1;
    color: var(--gold);
  }
  .holder-title {
    margin-top: 8px;
    font-size: 23px;
    line-height: 1;
  }
  .wordmark {
    position: absolute;
    left: 346px;
    top: 205px;
    width: 360px;
    text-align: center;
    font-family: "Cormorant Garamond", "Times New Roman", serif;
    font-weight: 600;
    color: var(--gold);
  }
  .wordmark-name {
    font-size: 70px;
    line-height: 1;
    letter-spacing: 2px;
  }
  .wordmark-rule {
    height: 3px;
    margin: 10px 0 8px;
    background: var(--gold);
  }
  .wordmark-place {
    font-size: 24px;
    letter-spacing: 3px;
    line-height: 1;
  }
  .contact {
    position: absolute;
    right: 48px;
    top: 410px;
    text-align: right;
    font-size: 23px;
    line-height: 1;
  }
  .contact-line + .contact-line { margin-top: 18px; }
  .contact-label { color: var(--gold-soft); }
  .contact-gap { display: inline-block; width: 12px; }
  .contact-web { color: var(--gold-soft); }
</style>
</head>
<body>
  <section class="business-card">
    <svg class="frost-band" viewBox="0 0 900 554" aria-hidden="true">
      <defs>
        <linearGradient id="frostFill" x1="0" y1="0" x2="1" y2="1">
          <stop offset="0" stop-color="var(--frost-b)"/>
          <stop offset="1" stop-color="var(--frost-a)"/>
        </linearGradient>
      </defs>
      <circle cx="194" cy="274" r="164" fill="url(#frostFill)"/>
      <rect x="194" y="163" width="706" height="215" fill="url(#frostFill)"/>
      <circle cx="194" cy="274" r="92" fill="none" stroke="var(--gold)" stroke-width="6"/>
    </svg>

    <header class="holder">
      <h1 class="holder-name">DARIO LORVANTI</h1>
      <p class="holder-title">CEO and CO Founder</p>
    </header>

    <div class="wordmark">
      <div class="wordmark-name">LORVANTI</div>
      <div class="wordmark-rule"></div>
      <div class="wordmark-place">ITALY</div>
    </div>

    <address class="contact" style="font-style: normal;">
      <p class="contact-line">4817 E Halvern</p>
      <p class="contact-line"><span class="contact-label">P:</span> 555-384-1926<span class="contact-gap"></span><span class="contact-label">F:</span> 555-384-1926</p>
      <p class="contact-line"><span class="contact-label">E:</span> dario@lorvanti.com<span class="contact-gap"></span><span class="contact-web">www.lorvanti.com</span></p>
    </address>
  </section>
</body>
</html>
```